New Business Card Design Project

Use the flyer uploaded and website www.brightoakbuilders.com for inspiration.
List Our Services on Backside of business cards
Marcus Delling
Harborline Builders Inc.
Licensed General Contractors
858-471-6093

Contact Information for Business Card

Use the flyer uploaded and website www.brightoakbuilders.com for inspiration. List Our Services on Backside of business cards Marcus Delling Harborline Builders Inc. Licensed General Contractors 858-471-6093

```html
<!DOCTYPE html>
<html lang="en">
<head>
<meta charset="UTF-8">
<title>Harborline Builders – Business Cards</title>
<link rel="stylesheet" href="https://fonts.googleapis.com/css2?family=Montserrat:wght@400;500;700&display=swap">
<style>
  :root {
    --page-bg: #2a2a2a;
    --card-bg: #1f1f1f;
    --card-edge: #2c2c2c;
    --ink: #f2f2f2;
    --ink-soft: #cfcfcf;
    --rule: #bdbdbd;
    --art-light: #8a8a8a;
    --art-dark: #1c1c1c;
  }
  * { box-sizing: border-box; margin: 0; padding: 0; }
  html, body { width: 1200px; height: 875px; overflow: hidden; }
  body {
    background: var(--page-bg);
    font-family: "Montserrat", sans-serif;
    color: var(--ink);
    display: flex;
    flex-direction: column;
    align-items: center;
    justify-content: center;
    gap: 48px;
  }
  .card {
    position: relative;
    width: 620px;
    height: 354px;
    background: var(--card-bg);
    border: 1px solid var(--card-edge);
    border-radius: 16px;
    overflow: hidden;
  }
  .brand-name {
    font-weight: 400;
    font-size: 25px;
    letter-spacing: 2px;
    text-transform: uppercase;
    color: var(--ink);
    white-space: nowrap;
  }
  .artwork {
    position: absolute;
    border-radius: 8px;
    background: radial-gradient(ellipse at 50% 25%, var(--art-light) 0%, #3a3a3a 40%, var(--art-dark) 80%);
    opacity: .85;
  }

  /* Front */
  .card--front .artwork { right: 24px; top: 16px; width: 230px; height: 140px; }
  .card--front .brand-name { position: absolute; left: 40px; top: 126px; }
  .card--front .divider-long {
    position: absolute; left: 40px; right: 24px; top: 190px;
    border-top: 1px solid var(--rule);
  }
  .licence { position: absolute; right: 28px; top: 166px; font-size: 11px; color: var(--ink-soft); }
  .identity { position: absolute; left: 40px; top: 204px; }
  .identity .person-name { font-weight: 700; font-size: 20px; line-height: 24px; }
  .identity .person-title { font-size: 12px; line-height: 15px; color: var(--ink-soft); margin-top: 2px; }
  .identity .divider-short { width: 190px; border-top: 1px solid var(--rule); margin-top: 8px; }
  .contact-list { position: absolute; left: 40px; top: 264px; list-style: none; display: grid; gap: 6px; }
  .contact-list li { display: flex; align-items: center; gap: 10px; font-size: 12px; line-height: 16px; color: var(--ink-soft); }
  .contact-list svg { width: 12px; height: 12px; fill: var(--ink); flex: none; }

  /* Back */
  .card--back .artwork { left: 20px; top: 70px; width: 250px; height: 270px; }
  .card--back .brand-name { position: absolute; right: 30px; top: 32px; }
  .services { position: absolute; left: 300px; top: 90px; }
  .services h2 { font-weight: 700; font-size: 16px; }
  .services .divider-short { width: 150px; border-top: 1px solid var(--rule); margin: 6px 0 10px; }
  .services ul { padding-left: 16px; font-size: 12.5px; line-height: 1.62; color: var(--ink-soft); }
</style>
</head>
<body>

  <section class="card card--front" aria-label="Business card front">
    <div class="artwork" role="img" aria-label="Palm tree and house outline illustration"></div>
    <div class="brand-name">Harborline Builders</div>
    <div class="licence">CSLB Licensed No. #4820516</div>
    <div class="divider-long"></div>
    <div class="identity">
      <div class="person-name">Marcus Delling</div>
      <div class="person-title">Managing Director</div>
      <div class="divider-short"></div>
    </div>
    <ul class="contact-list">
      <li>
        <svg viewBox="0 0 24 24" aria-hidden="true"><path d="M6.6 10.8a15.5 15.5 0 0 0 6.6 6.6l2.2-2.2c.3-.3.7-.4 1-.2 1.1.4 2.3.6 3.6.6.6 0 1 .4 1 1V20c0 .6-.4 1-1 1A17 17 0 0 1 3 4c0-.6.4-1 1-1h3.5c.6 0 1 .4 1 1 0 1.3.2 2.5.6 3.6.1.3 0 .7-.2 1l-2.3 2.2z"/></svg>
        858-471-6093
      </li>
      <li>
        <svg viewBox="0 0 24 24" aria-hidden="true"><path d="M2 5h20v14H2V5zm2 2v.5l8 5 8-5V7H4zm0 2.8V17h16V9.8l-8 5-8-5z"/></svg>
        info@brightoakbuilders.com
      </li>
      <li>
        <svg viewBox="0 0 24 24" aria-hidden="true"><path d="M12 2a10 10 0 1 0 0 20 10 10 0 0 0 0-20zm6.9 9h-3a15 15 0 0 0-1.3-5.8A8 8 0 0 1 18.9 11zM12 4c.9 1.2 1.8 3.6 1.9 7h-3.8C10.2 7.6 11.1 5.2 12 4zM9.4 5.2A15 15 0 0 0 8.1 11h-3a8 8 0 0 1 4.3-5.8zM5.1 13h3a15 15 0 0 0 1.3 5.8A8 8 0 0 1 5.1 13zM12 20c-.9-1.2-1.8-3.6-1.9-7h3.8c-.1 3.4-1 5.8-1.9 7zm2.6-1.2a15 15 0 0 0 1.3-5.8h3a8 8 0 0 1-4.3 5.8z"/></svg>
        www.brightoakbuilders.com
      </li>
    </ul>
  </section>

  <section class="card card--back" aria-label="Business card back">
    <div class="artwork" role="img" aria-label="Palm tree and house outline illustration"></div>
    <div class="brand-name">Harborline Builders</div>
    <div class="services">
      <h2>Our Services</h2>
      <div class="divider-short"></div>
      <ul>
        <li>Remodel: Kitchen &amp; Bath</li>
        <li>Painting: Interior &amp; Exterior</li>
        <li>Flooring: Carpet, Vinyl, Wood</li>
        <li>Window: Door Replacement</li>
        <li>Plumbing: Repair &amp; Upgrades</li>
        <li>Energy Efficienct Upgrades</li>
        <li>Deck &amp; Patio construction</li>
        <li>Water &amp; Mold Damage</li>
        <li>Garage Renovation</li>
      </ul>
    </div>
  </section>

</body>
</html>
```